Coastal Gin Label Design

We are needing a nautical/coastal themed label for our upcoming gin release.

We have saltbush, cucumber, juniper, and quandong being used in this gin.

Name of the Gin; Harbour Moons

The logo attached is the company logo, but doesn't have to be used on the front of the label, ie it can just be the name Fernwhistle somewhere on the front.
Bottle specs attached as well so you can accurately represent the bottle- this bottle is also clear.

Target Market(s)

Women 25- 45

Font styles to use
Serif
Decorative

Colors
d5edf4
86cae7
33a6d7
86cfc6
cfeae6
ffffff
f6faec
ecf7fb
fefeff

Requirements
Must have
• Ocean/Coastal vibe to the label
Nice to have
• Blues,Whites clean and crisp
Should not have
• No generic word art look to it.
A dark mood

```html
<!DOCTYPE html>
<html lang="en">
<head>
<meta charset="utf-8">
<title>Fernwhistle Harbour Moons Gin Label</title>
<link rel="stylesheet" href="https://fonts.googleapis.com/css2?family=Cinzel:wght@500&family=Josefin+Sans:wght@600&family=Oswald:wght@300&family=Titan+One&display=swap">
<style>
  :root {
    --page: #ffffff;
    --sea-deep: #0f9c92;
    --sea: #3dbfb6;
    --sea-light: #86cfc6;
    --sand: #ecdcb8;
    --foam: #fefeff;
    --gold: #b8973e;
    --ink-teal: #0b6e73;
    --mid-teal: #13a096;
    --light-teal: #5cc3bd;
    --white: #ffffff;
  }
  html, body {
    margin: 0;
    width: 1200px;
    height: 1193px;
    overflow: hidden;
    background: var(--page);
  }
  .canvas {
    position: relative;
    width: 1200px;
    height: 1193px;
  }
  .label {
    position: absolute;
    left: 341px;
    top: 291px;
    width: 530px;
    height: 673px;
    overflow: hidden;
    box-shadow: 0 4px 14px rgba(0,0,0,0.18);
  }
  .label__shore {
    position: absolute;
    inset: 0;
    background: linear-gradient(148deg,
      var(--sea) 0%,
      var(--sea-light) 14%,
      var(--sand) 26%,
      var(--foam) 36%,
      var(--foam) 60%,
      var(--sand) 68%,
      var(--sea-light) 76%,
      var(--sea) 86%,
      var(--sea-deep) 100%);
  }
  .label__maker {
    position: absolute;
    left: 189px;
    top: 160px;
    transform: translate(-50%, -50%) rotate(-25deg);
    font-family: "Cinzel", serif;
    font-weight: 500;
    font-size: 36px;
    letter-spacing: 1px;
    text-transform: uppercase;
    color: var(--gold);
    white-space: nowrap;
  }
  .label__name {
    margin: 0;
    font-family: "Titan One", sans-serif;
    font-weight: 400;
    text-transform: uppercase;
    line-height: 1;
  }
  .label__name-line {
    position: absolute;
    transform: translate(-50%, -50%) rotate(-22deg);
    white-space: nowrap;
    background: linear-gradient(20deg, var(--ink-teal) 0%, var(--mid-teal) 60%, var(--light-teal) 100%);
    -webkit-background-clip: text;
    background-clip: text;
    color: transparent;
  }
  .label__name-line--first {
    left: 236px;
    top: 216px;
    font-size: 70px;
  }
  .label__name-line--second {
    left: 282px;
    top: 334px;
    font-size: 86px;
  }
  .label__spirit {
    position: absolute;
    left: 0;
    right: 0;
    top: 472px;
    text-align: center;
    font-family: "Josefin Sans", sans-serif;
    font-weight: 600;
    font-size: 66px;
    line-height: 1;
    letter-spacing: 12px;
    padding-left: 12px;
    color: var(--white);
    text-shadow: 0 2px 4px rgba(0,0,0,0.25);
  }
  .label__rule {
    position: absolute;
    left: 139px;
    width: 250px;
    top: 577px;
    height: 2px;
    background: var(--white);
  }
  .label__specs {
    position: absolute;
    left: 139px;
    width: 250px;
    top: 586px;
    display: flex;
    justify-content: center;
    gap: 25px;
    font-family: "Oswald", sans-serif;
    font-weight: 300;
    font-size: 25px;
    line-height: 1.2;
    color: var(--white);
  }
</style>
</head>
<body>
<main class="canvas">
  <section class="label">
    <div class="label__shore" role="img" aria-label="Aerial photograph of turquoise surf washing over a pale sandy beach"></div>
    <div class="label__maker">Fernwhistle</div>
    <h1 class="label__name">
      <span class="label__name-line label__name-line--first">Harbour</span>
      <span class="label__name-line label__name-line--second">Moons</span>
    </h1>
    <div class="label__spirit">GIN</div>
    <div class="label__rule"></div>
    <div class="label__specs"><span>42% ALC/VOL</span><span>750ML</span></div>
  </section>
</main>
</body>
</html>
```